American cannabis tech company business card design

Pavrel.com is seeking a modern, professional, and brand-aligned business card that represents our company and its core values: Mission, Story, Values, and Impact. As an innovative cannabis company, we want a business card that is not only visually appealing but also serves as a representation of who we are and what we stand for.

Project Scope: Design a double-sided business card that integrates our brand identity and core values. Incorporate our key brand elements, ensuring a sleek and contemporary aesthetic. Visually reflect our core values (Mission, Story, Values, Impact) in a way that is engaging yet professional.

Target Market(s)

Vendors, third parties,

Contact Information for Business Card

Contact details (name, title, email, phone, website, etc.)

Font styles to use
Other font styles liked:
• Caslon, Centra

Colors

Designer to choose colors to be used in the design.

Requirements
Must have
• Pavrel.com logo and branding A creative yet clean way to integrate our core values (Mission, Story, Values, Impact) Modern typography and a well-structured layout
Nice to have
• forest green, grey, white, black
Should not have
• references to marijuana, leafs, plants, or related product

```html
<!DOCTYPE html>
<html lang="en">
<head>
<meta charset="UTF-8">
<title>Pavrel Business Card</title>
<link rel="stylesheet" href="https://fonts.googleapis.com/css2?family=Poppins:wght@400;500;600;800&display=swap">
<style>
  :root {
    --forest: #1b4a22;
    --forest-deep: #163a1b;
    --ink-green: #17401d;
    --paper: #ffffff;
    --backdrop: #d6d6d6;
    --soft-grey: #c9c9c9;
    --values-grey: #a9bfa9;
    --watermark-light: rgba(255,255,255,0.05);
    --watermark-dark: rgba(0,0,0,0.045);
  }
  * { margin: 0; padding: 0; box-sizing: border-box; }
  html, body { width: 1200px; height: 900px; overflow: hidden; }
  body {
    background: var(--backdrop);
    font-family: "Poppins", sans-serif;
    position: relative;
  }
  .card {
    position: absolute;
    width: 520px;
    height: 298px;
    border-radius: 24px;
    overflow: hidden;
  }
  .watermark {
    position: absolute;
    font-weight: 800;
    line-height: 1;
    white-space: nowrap;
  }

  /* Front */
  .card-front {
    left: 90px; top: 110px;
    background: linear-gradient(160deg, var(--forest) 0%, var(--forest-deep) 100%);
  }
  .card-front .watermark {
    right: -30px; bottom: -52px;
    font-size: 104px;
    color: var(--watermark-light);
  }
  .card-front .brand-name {
    position: absolute;
    left: 0; right: 0; top: 78px;
    text-align: center;
    font-weight: 800;
    font-size: 78px;
    line-height: 1;
    letter-spacing: 1px;
    color: var(--soft-grey);
  }
  .card-front .core-values {
    position: absolute;
    left: 0; right: 0; top: 180px;
    text-align: center;
    font-size: 11px;
    font-weight: 500;
    line-height: 1;
    letter-spacing: 3px;
    text-transform: uppercase;
    color: var(--values-grey);
  }
  .card-front .core-values span + span::before {
    content: "·";
    margin: 0 10px;
  }
  .card-front .site {
    position: absolute;
    left: 0; right: 0; top: 222px;
    text-align: center;
    font-size: 15px;
    line-height: 1;
    letter-spacing: 1px;
    color: #ffffff;
  }

  /* Back */
  .card-back {
    left: 590px; top: 490px;
    background: var(--paper);
  }
  .card-back .watermark {
    right: -30px; top: 90px;
    font-size: 80px;
    color: var(--watermark-dark);
  }
  .card-back .site {
    position: absolute;
    right: 34px; top: 34px;
    font-size: 13px;
    font-weight: 600;
    line-height: 1;
    color: var(--ink-green);
  }
  .card-back .brand-name {
    position: absolute;
    left: 38px; top: 40px;
    font-weight: 800;
    font-size: 62px;
    line-height: 1;
    color: var(--ink-green);
  }
  .identity {
    position: absolute;
    left: 50px; top: 160px;
    color: var(--ink-green);
  }
  .identity .accent-block {
    position: absolute;
    left: -50px; top: 4px;
    width: 36px; height: 36px;
    background: var(--ink-green);
  }
  .identity .person-name {
    font-weight: 600;
    font-size: 21px;
    line-height: 1.1;
    letter-spacing: .5px;
  }
  .identity .person-title {
    font-size: 16px;
    line-height: 1.2;
  }
  .contacts {
    position: absolute;
    left: 50px; top: 222px;
    list-style: none;
    color: var(--ink-green);
    font-size: 17px;
  }
  .contacts li {
    display: flex;
    align-items: center;
    gap: 8px;
    height: 28px;
  }
  .contacts svg { width: 22px; height: 22px; flex: none; }
</style>
</head>
<body>
  <section class="card card-front">
    <div class="watermark" aria-hidden="true">PAVREL</div>
    <div class="brand-name">PAVREL</div>
    <p class="core-values"><span>Mission</span><span>Story</span><span>Values</span><span>Impact</span></p>
    <div class="site">www.Pavrel.com</div>
  </section>

  <section class="card card-back">
    <div class="watermark" aria-hidden="true">PAVREL</div>
    <div class="site">www.Pavrel.com</div>
    <div class="brand-name">PAVREL</div>
    <div class="identity">
      <span class="accent-block"></span>
      <p class="person-name">ELENA MARSH</p>
      <p class="person-title">Managing Director</p>
    </div>
    <ul class="contacts">
      <li>
        <svg viewBox="0 0 22 22" aria-hidden="true">
          <circle cx="11" cy="11" r="11" fill="#17401d"/>
          <path d="M7.5 6.5c.6-.5 1.3-.4 1.6.2l.8 1.5c.2.5.1 1-.3 1.3l-.6.5c.5 1.2 1.4 2.1 2.6 2.6l.5-.6c.3-.4.8-.5 1.3-.3l1.5.8c.6.3.7 1 .2 1.6l-.7.7c-.6.6-1.6.7-2.4.3-2.3-1.1-4-2.8-5.1-5.1-.4-.8-.3-1.8.3-2.4z" fill="#fff"/>
        </svg>
        <span>044-555 018 274</span>
      </li>
      <li>
        <svg viewBox="0 0 22 22" aria-hidden="true">
          <circle cx="11" cy="11" r="11" fill="#17401d"/>
          <rect x="5.5" y="7" width="11" height="8" rx="1" fill="#fff"/>
          <path d="M5.8 7.4 11 11.6l5.2-4.2" fill="none" stroke="#17401d" stroke-width="1"/>
        </svg>
        <span>hello@pavrel.com</span>
      </li>
    </ul>
  </section>
</body>
</html>
```